Design website for new email startup

We are starting a company called Pingo.QZ (it will live at http://pingo.qz).

We would like the main landing page for our site designed. We have provided a very simple wireframe to help provide direction for the content it should include, but we do not expect the designers to adhere to it at all - we encourage unique ideas. There is some sample text in the wireframe - this does not have to be used, but may provide ideas.

We provide an easy way for people to manage email for a custom domain name. For example if you own "yourhouseword.example" you can point your DNS records to us and we'll make it easy to have emails addressed to your domain get forwarded to your existing email (gmail, etc). Folks running blogs, and other small sites can quickly setup email addresses for their domains and manage them in one place.

(For technical folks, we have you point your dns mx records to us, hence the name. That way all your email hits us and we can redirect it wherever you want. We make it easy to manage a single domain or a bunch of domains. Many domain registrars offer this service for a fee, and have clumsy management tools. We provide a robust simple toolset for free, as well as premium options).

The goal of the landing page is to get folks into the signup flow. The second priority flow is to have them take a look at the premium plan offerings.

We may offer the winning designer additional work for the remainder of the site design.
Updates

I've changed this project to a committed payment.  It is no longer refundable.  Thank you.

Target Market(s)

Bloggers, podcasters, designers, app developers - people who are a little tech savvy.

Industry/Entity Type

It Company

Font styles to use
Sans Serif

Colors

Designer to choose colors to be used in the design.

Requirements
Must have
• A full fidelity mockup (comp) of the landing page including the source file (psd, ai, etc).

Some sort of logo treatment for the pingo.qz brand

A call to action for signup, such as the suggested 'Get Started Here'
Nice to have
• A hip startup feel

Incorporation of the email theme

Give the impression it is simple, easy and fast

```html
<!DOCTYPE html>
<html lang="en">
<head>
<meta charset="utf-8">
<title>Pingo.QZ — We make email easy</title>
<link href="https://fonts.googleapis.com/css2?family=Open+Sans:wght@400;600&family=Archivo+Narrow:wght@700&display=swap" rel="stylesheet">
<style>
  :root {
    --brand-green: #4fb81c;
    --green-top: #66cc2a;
    --green-bottom: #3f9e12;
    --cta-red: #d10a0a;
    --ink: #2f2f2f;
    --nav-grey: #555b61;
    --body-grey: #6f6f6f;
    --footer-bg: #d6d6d6;
    --footer-ink: #5d6570;
    --hero-dark: #2a3440;
    --hero-mid: #7d8d99;
    --hero-light: #c9d2d8;
    --white: #ffffff;
  }
  * { box-sizing: border-box; margin: 0; padding: 0; }
  html, body { width: 1200px; height: 1026px; overflow: hidden; background: var(--white); }
  body { position: relative; font-family: "Open Sans", Arial, sans-serif; }

  .site-header { position: absolute; left: 0; top: 0; width: 1200px; height: 119px; background: var(--white); }
  .brand { position: absolute; left: 53px; top: 42px; display: flex; align-items: center; gap: 12px; text-decoration: none; }
  .brand-mark { width: 30px; height: 30px; background: var(--nav-grey); }
  .brand-name { font-size: 32px; font-weight: 400; color: var(--brand-green); letter-spacing: 0.5px; }
  .main-nav { position: absolute; right: 54px; top: 59px; display: flex; gap: 13px; }
  .main-nav a { font-size: 13px; color: var(--nav-grey); text-decoration: none; text-transform: uppercase; }
  .main-nav a.is-active { color: var(--brand-green); }

  .hero { position: absolute; left: 0; top: 119px; width: 1200px; height: 505px; overflow: hidden; }
  .hero-photo { position: absolute; inset: 0;
    background: radial-gradient(ellipse 520px 360px at 760px 200px, var(--hero-light) 0%, var(--hero-mid) 45%, var(--hero-dark) 100%); }
  .hero-arrow { position: absolute; top: 206px; width: 41px; height: 47px; background: #111; display: flex; align-items: center; justify-content: center; }
  .hero-arrow--prev { left: 12px; }
  .hero-arrow--next { right: 12px; }
  .hero-title { position: absolute; left: 113px; top: 253px; font-family: "Archivo Narrow", "Arial Narrow", sans-serif; font-weight: 700; font-size: 39px; color: var(--white); text-shadow: 0 1px 3px rgba(0,0,0,.35); }
  .cta { position: absolute; top: 346px; height: 48px; display: flex; align-items: center; gap: 12px; padding: 0 16px; color: var(--white); text-decoration: none; font-size: 16px; }
  .cta--signup { left: 116px; width: 196px; background: linear-gradient(var(--green-top), var(--green-bottom)); font-weight: 600; }
  .cta--plans { left: 322px; width: 177px; background: var(--cta-red); }

  .features { position: absolute; left: 0; top: 624px; width: 1200px; height: 291px; }
  .feature { position: absolute; top: 80px; width: 560px; }
  .feature--dns { left: 65px; }
  .feature--registrar { left: 655px; }
  .feature-badge { position: absolute; left: 0; top: 12px; width: 120px; height: 60px; border-radius: 30px; background: #333; }
  .feature--registrar .feature-badge { left: 12px; top: 0; width: 86px; height: 130px; border-radius: 6px; background: linear-gradient(#e8a03c, #f2f2d8); }
  .feature-title { margin-left: 155px; font-size: 16.5px; font-weight: 600; line-height: 25px; color: var(--brand-green); }
  .feature--registrar .feature-title { margin-left: 124px; }
  .feature-text { margin-left: 155px; margin-top: 1px; width: 357px; font-size: 13px; line-height: 23px; color: var(--body-grey); text-align: justify; }
  .feature--registrar .feature-text { margin-left: 124px; }

  .site-footer { position: absolute; left: 0; top: 915px; width: 1200px; height: 111px; background: var(--footer-bg); }
  .footer-nav { position: absolute; left: 0; width: 1200px; top: 31px; text-align: center; font-size: 13px; color: var(--footer-ink); padding-left: 40px; }
  .footer-nav a { color: var(--footer-ink); text-decoration: none; margin: 0 6px; }
  .copyright { position: absolute; left: 0; width: 1200px; top: 58px; text-align: center; font-size: 13px; color: var(--footer-ink); padding-left: 40px; }
  .social { position: absolute; right: 54px; top: 29px; display: flex; gap: 9px; }
  .social span { width: 28px; height: 28px; border-radius: 3px; background: #4a78b8; }
</style>
</head>
<body>
  <header class="site-header">
    <a class="brand" href="http://pingo.qz">
      <span class="brand-mark"></span>
      <span class="brand-name">PINGO.QZ</span>
    </a>
    <nav class="main-nav">
      <a class="is-active" href="#">How it works</a>
      <a href="#">Support</a>
      <a href="#">Login</a>
    </nav>
  </header>

  <section class="hero">
    <div class="hero-photo" role="img" aria-label="Photo of a finger touching a glowing open envelope with a green @ card, over a soft blue-grey background of faint envelopes"></div>
    <a class="hero-arrow hero-arrow--prev" href="#" aria-label="Previous slide">
      <svg width="12" height="26" viewBox="0 0 12 26"><path d="M10 1 L2 13 L10 25" fill="none" stroke="#fff" stroke-width="1.5"/></svg>
    </a>
    <a class="hero-arrow hero-arrow--next" href="#" aria-label="Next slide">
      <svg width="12" height="26" viewBox="0 0 12 26"><path d="M2 1 L10 13 L2 25" fill="none" stroke="#fff" stroke-width="1.5"/></svg>
    </a>
    <h1 class="hero-title">We make email easy</h1>
    <a class="cta cta--signup" href="#">GET STARTED FREE
      <svg width="9" height="13" viewBox="0 0 9 13"><path d="M2 1.5 L7 6.5 L2 11.5" fill="none" stroke="#fff" stroke-width="2.6"/></svg>
    </a>
    <a class="cta cta--plans" href="#">COMPARE PLANS
      <svg width="9" height="13" viewBox="0 0 9 13"><path d="M2 1.5 L7 6.5 L2 11.5" fill="none" stroke="#fff" stroke-width="2.6"/></svg>
    </a>
  </section>

  <section class="features">
    <article class="feature feature--dns">
      <div class="feature-badge" role="img" aria-label="SkyVeil partner badge"></div>
      <h2 class="feature-title">How to configure your SkyVeil DNS<br>to use pingo.qz</h2>
      <p class="feature-text">Lorem ipsum dolor sit amet, consectetur adipisicing elit, sed do eiusmod tempor incididunt ut labore et dolore magna aliqua. Ut enim ad minim veniam, quis nostrud exercitation ullamco laboris nisi ut aliquip commodo consequat.</p>
    </article>
    <article class="feature feature--registrar">
      <div class="feature-badge" role="img" aria-label="NameBarn partner badge"></div>
      <h2 class="feature-title">Use pingo.qz with your NameBarn domain<br>registration for reliable email forwarding</h2>
      <p class="feature-text">Lorem ipsum dolor sit amet, consectetur adipisicing elit, sed do eiusmod tempor incididunt ut labore et dolore magna aliqua. Ut enim ad minim veniam, quis nostrud exercitation ullamco laboris nisi ut aliquip commodo consequat.</p>
    </article>
  </section>

  <footer class="site-footer">
    <nav class="footer-nav">
      <a href="#">Home</a>|<a href="#">How it works</a>|<a href="#">Support</a>|<a href="#">Terms &amp; Use</a>|<a href="#">Privacy</a>
    </nav>
    <p class="copyright">All Rights reserved. copyrights @ 2013 pingo.qz</p>
    <div class="social" aria-label="Social links">
      <span></span><span></span><span></span>
    </div>
  </footer>
</body>
</html>
```